i need a business card for a plumbing company in california

we are a drain cleaning , maintenance plumbing company who is starting new marketing campaign for a tatrench-less pipe installation department .

Target Market(s)

the professional who appreciates time and quality workmanship.

Industry/Entity Type

Plumbing

Colors
0655a3
ec1f27

Requirements
Must have
• the second logo needs to be included
Nice to have
• a focus on the services offered
Should not have
• any underlined words on the brief

```html
<!DOCTYPE html>
<html lang="en">
<head>
<meta charset="utf-8">
<title>Topgrade Plumbing – Business Card</title>
<link href="https://fonts.googleapis.com/css2?family=Arimo:wght@400;700&family=Exo+2:wght@700&display=swap" rel="stylesheet">
<style>
  :root {
    --stage: #2e2e2e;
    --paper: #ffffff;
    --stone: #7e7b6f;
    --signal-red: #e0232a;
    --ink: #222222;
    --ink-soft: #555555;
  }
  * { margin: 0; padding: 0; box-sizing: border-box; }
  html, body { width: 1200px; height: 782px; overflow: hidden; }
  body {
    background: var(--stage);
    font-family: "Arimo", Arial, sans-serif;
    position: relative;
  }
  .card {
    position: absolute;
    width: 560px;
    height: 320px;
    background: var(--paper);
    box-shadow: 0 10px 30px rgba(0,0,0,.45);
    overflow: hidden;
  }
  .card svg.card-shapes { position: absolute; inset: 0; }
  .card-front { left: 560px; top: 60px; }
  .card-back { left: 80px; top: 410px; }

  .brand-name {
    font-family: "Exo 2", Arial, sans-serif;
    font-weight: 700;
    line-height: 0.95;
  }

  /* front */
  .front-square {
    position: absolute; left: 70px; top: 110px;
    width: 100px; height: 100px; background: var(--signal-red);
  }
  .front-name {
    position: absolute; left: 290px; top: 104px;
    color: var(--paper); font-size: 46px;
  }

  /* back */
  .holder { position: absolute; left: 44px; top: 32px; }
  .holder-name {
    color: var(--signal-red); font-weight: 700; font-size: 17px; letter-spacing: .3px;
  }
  .holder-role { color: var(--ink-soft); font-size: 12px; margin-top: 2px; }

  .contact-list {
    position: absolute; left: 26px; top: 150px; list-style: none;
    font-size: 14px; color: var(--ink);
  }
  .contact-list li { display: flex; align-items: center; gap: 7px; height: 20px; }
  .contact-list svg { width: 11px; height: 11px; fill: var(--signal-red); flex: none; }

  .back-brand {
    position: absolute; right: 34px; top: 104px;
    display: flex; align-items: center; gap: 12px;
  }
  .back-brand-square { width: 34px; height: 34px; background: var(--signal-red); }
  .back-brand-name { color: var(--stone); font-size: 34px; }

  .address {
    position: absolute; right: 34px; top: 212px; text-align: right;
    font-size: 15px; color: var(--ink); line-height: 1.35;
  }
</style>
</head>
<body>

<section class="card card-front" aria-label="Card front">
  <svg class="card-shapes" viewBox="0 0 560 320" width="560" height="320" aria-hidden="true">
    <polygon points="230,0 560,0 560,320 270,320" fill="var(--stone)"/>
  </svg>
  <div class="front-square"></div>
  <div class="front-name brand-name">Topgrade<br>Plumbing</div>
</section>

<section class="card card-back" aria-label="Card back">
  <svg class="card-shapes" viewBox="0 0 560 320" width="560" height="320" aria-hidden="true">
    <polygon points="12,58 36,26 36,58" fill="var(--signal-red)"/>
    <polygon points="0,262 268,262 240,320 0,320" fill="var(--stone)"/>
    <polygon points="268,288 560,288 560,320 252,320" fill="var(--signal-red)"/>
  </svg>

  <div class="holder">
    <div class="holder-name">MARCUS DELGADO</div>
    <div class="holder-role">Managing Director</div>
  </div>

  <ul class="contact-list">
    <li><svg viewBox="0 0 12 12"><path d="M2 1h3l1 3-2 1a7 7 0 0 0 3 3l1-2 3 1v3c-6 0-10-4-9-9z"/></svg>044-987 654 321</li>
    <li><svg viewBox="0 0 12 12"><path d="M3 0h6v12H3zM4 1v9h4V1z"/></svg>044-987 654 322</li>
    <li><svg viewBox="0 0 12 12"><path d="M0 2h12v8H0zM1 3l5 4 5-4z"/></svg>hello@topgradeplumb.com</li>
    <li><svg viewBox="0 0 12 12"><circle cx="6" cy="6" r="6"/></svg>www.topgradeplumb.com</li>
  </ul>

  <div class="back-brand">
    <div class="back-brand-name brand-name">Topgrade<br>Plumbing</div>
    <div class="back-brand-square"></div>
  </div>

  <div class="address">480 Harbor Lane, Suite 2<br>Oakridge, CA 95012</div>
</section>

</body>
</html>
```